I am looking for a modern, clean and neat design for a reflexology and well being business. The business name is Gralo Tund (this is an old Latin word for wellbeing). The colours I would like are purple, white and grey. I am open to suggestions for pictures such as healing or working hands, a pair of feet, images that represent my business that you may think of....... or maybe you think no images at all would be best? My tag line is: "Relax, Renew, Revive" or "Find you balance......... Relax, Renew, Revive" I can decide which I want so I would like to see what both would look like. I would like space on the back to write the client's appointment date and time (more than once)

```html
<!DOCTYPE html>
<html lang="en">
<head>
<meta charset="utf-8">
<title>Gralo Tund – Business Card</title>
<link rel="stylesheet" href="https://fonts.googleapis.com/css2?family=Open+Sans:wght@400;600;700&display=swap">
<style>
  :root {
    --bg: #2b2b2d;
    --card-dark: #545456;
    --card-light: #ffffff;
    --lavender: #a1b8e0;
    --stripe-grey: #555557;
    --text-grey: #555557;
    --text-white: #ffffff;
  }
  * { box-sizing: border-box; margin: 0; padding: 0; }
  html, body {
    width: 1200px; height: 900px; overflow: hidden;
    background: var(--bg);
    font-family: "Open Sans", sans-serif;
  }
  .canvas { position: relative; width: 1200px; height: 900px; }
  .card {
    position: absolute; width: 560px; height: 320px;
    border-radius: 20px; overflow: hidden;
    box-shadow: 0 12px 30px rgba(0,0,0,.45);
  }

  /* Back card */
  .card-back { left: 70px; top: 90px; background: var(--card-dark); color: var(--text-white); }
  .brand-block {
    position: absolute; right: 34px; top: 34px;
    display: flex; flex-direction: column; align-items: flex-end; gap: 8px;
  }
  .brand-name {
    display: flex; align-items: center; gap: 10px;
    font-size: 30px; font-weight: 600; color: var(--lavender); letter-spacing: .5px;
  }
  .brand-dot { width: 22px; height: 22px; border-radius: 50%; background: var(--lavender); }
  .tagline { font-size: 12px; font-weight: 600; letter-spacing: .8px; text-transform: uppercase; }
  .appointment { position: absolute; left: 34px; bottom: 34px; width: 420px; }
  .appointment-title { font-size: 17px; font-weight: 700; margin-bottom: 10px; }
  .appointment-row { display: flex; align-items: flex-end; font-size: 12px; margin-top: 12px; }
  .appointment-row .field-line {
    flex: 1; margin-left: 4px; border-bottom: 2px dotted rgba(255,255,255,.8); height: 1px;
  }

  /* Front card */
  .card-front { left: 590px; top: 490px; background: var(--card-light); }
  .front-shapes { position: absolute; inset: 0; z-index: 0; }
  .front-brand {
    position: absolute; left: 36px; top: 92px; z-index: 1;
    display: flex; align-items: center; gap: 12px;
    font-size: 30px; font-weight: 600; color: var(--text-grey); letter-spacing: .5px;
  }
  .front-brand .brand-dot { width: 26px; height: 26px; }
  .person { position: absolute; right: 140px; top: 22px; text-align: right; z-index: 1; }
  .person-name { font-size: 18px; font-weight: 600; color: var(--lavender); letter-spacing: 1px; text-transform: uppercase; white-space: nowrap; }
  .person-role { font-size: 10px; font-weight: 600; color: var(--text-grey); letter-spacing: .8px; text-transform: uppercase; }
  .contact {
    position: absolute; right: 22px; bottom: 86px; z-index: 1;
    display: flex; flex-direction: column; align-items: flex-end; gap: 5px;
    font-size: 12px; color: var(--text-white);
  }
  .contact-item { display: flex; align-items: center; gap: 8px; }
  .contact-item svg { width: 11px; height: 11px; fill: var(--stripe-grey); }
</style>
</head>
<body>
<main class="canvas">

  <section class="card card-back" aria-label="Card back">
    <div class="brand-block">
      <div class="brand-name"><span class="brand-dot"></span>Gralo Tund</div>
      <div class="tagline">Relax, Renew, Revive</div>
    </div>
    <div class="appointment">
      <div class="appointment-title">Appointment:</div>
      <div class="appointment-row"><span>Name:</span><span class="field-line"></span></div>
      <div class="appointment-row"><span>Time:</span><span class="field-line"></span></div>
      <div class="appointment-row"><span>Date:</span><span class="field-line"></span></div>
    </div>
  </section>

  <section class="card card-front" aria-label="Card front">
    <svg class="front-shapes" viewBox="0 0 560 320" preserveAspectRatio="none">
      <path fill="var(--lavender)" d="M0,320 L0,288 C210,262 440,205 492,0 L560,0 L560,320 Z"/>
      <path fill="var(--stripe-grey)" d="M0,262 C215,250 430,185 470,0 L484,0 C432,196 210,260 0,282 Z"/>
    </svg>
    <div class="front-brand"><span class="brand-dot"></span>Gralo Tund</div>
    <div class="person">
      <div class="person-name">Mara Velin</div>
      <div class="person-role">Director</div>
    </div>
    <div class="contact">
      <div class="contact-item">+330 5550-1842
        <svg viewBox="0 0 24 24"><path d="M6.6 10.8a15 15 0 0 0 6.6 6.6l2.2-2.2a1 1 0 0 1 1-.25 11.4 11.4 0 0 0 3.6.57 1 1 0 0 1 1 1V20a1 1 0 0 1-1 1A17 17 0 0 1 3 4a1 1 0 0 1 1-1h3.5a1 1 0 0 1 1 1c0 1.250.2 2.45.57 3.57a1 1 0 0 1-.25 1z"/></svg>
      </div>
      <div class="contact-item">info@gralotund.com
        <svg viewBox="0 0 24 24"><path d="M2 5h20v14H2z M4 7v.5l8 5 8-5V7z" fill-rule="evenodd"/></svg>
      </div>
      <div class="contact-item">www.gralotund.com
        <svg viewBox="0 0 24 24"><circle cx="12" cy="12" r="10"/></svg>
      </div>
    </div>
  </section>

</main>
</body>
</html>
```